Meadowlark Property Review is a leading provider of residential appraisal and home inspection products in S

I need a business card/logo designed that obviously describes my business. We are a residential appraisal and home inspection company in Springfield, MO. We offer residential appraisals, home inspection, pest inspection and radon gas measurement. We have been in business for 18 years and hold state certified residential appraisal licenses and OBREX certified home inspection licenses. I have a logo that I really like and will attach, but would be open to new suggestions. I like more modern designs than traditional and would like a two sided card with our services, licenses and qualifications on the back.

```html
<!DOCTYPE html>
<html lang="en">
<head>
<meta charset="utf-8">
<title>Meadowlark Property Review — Business Card</title>
<link rel="stylesheet" href="https://fonts.googleapis.com/css2?family=Source+Sans+3:ital,wght@0,400;0,600;0,700;1,400&display=swap">
<style>
  :root {
    --page-bg: #e6e2dd;
    --card-light: #f3f1ee;
    --brown-dark: #4a3628;
    --brown-mid: #6b4e3a;
    --brand-brown: #6e5644;
    --accent-orange: #e2772a;
    --text-light: #f5efe8;
    --text-name: #6b5a4c;
  }
  * { margin: 0; padding: 0; box-sizing: border-box; }
  html, body {
    width: 1200px;
    height: 969px;
    overflow: hidden;
    background: var(--page-bg);
    font-family: "Source Sans 3", "Segoe UI", sans-serif;
  }
  .canvas {
    position: relative;
    width: 1200px;
    height: 969px;
  }
  .business-card {
    position: absolute;
    left: 100px;
    top: 200px;
    width: 1000px;
    height: 570px;
    border-radius: 26px;
    overflow: hidden;
    background: var(--card-light);
    box-shadow: 0 18px 40px rgba(60, 40, 25, 0.18);
  }
  .card-shapes {
    position: absolute;
    inset: 0;
  }
  .brand-name {
    position: absolute;
    left: 96px;
    top: 150px;
    font-size: 40px;
    font-weight: 700;
    letter-spacing: -0.5px;
    color: var(--brand-brown);
  }
  .person {
    position: absolute;
    left: 98px;
    top: 295px;
  }
  .person-name {
    font-size: 33px;
    font-weight: 600;
    color: var(--text-name);
    line-height: 1.2;
  }
  .person-title {
    font-size: 26px;
    color: var(--accent-orange);
    line-height: 1.3;
  }
  .contact-block {
    position: absolute;
    right: 28px;
    top: 248px;
    text-align: right;
    color: var(--text-light);
  }
  .address {
    font-size: 23px;
    line-height: 31px;
    margin-right: 28px;
    margin-bottom: 18px;
  }
  .contact-line {
    display: flex;
    justify-content: flex-end;
    align-items: center;
    gap: 14px;
    font-size: 23px;
    height: 39px;
  }
  .contact-icon {
    width: 24px;
    height: 24px;
    fill: var(--text-light);
  }
  .services {
    position: absolute;
    right: 28px;
    top: 486px;
    text-align: right;
    font-style: italic;
    font-size: 23px;
    line-height: 33px;
    color: var(--text-light);
  }
</style>
</head>
<body>
<main class="canvas">
  <section class="business-card" aria-label="Meadowlark Property Review business card">
    <svg class="card-shapes" width="1000" height="570" viewBox="0 0 1000 570" aria-hidden="true">
      <defs>
        <linearGradient id="brownPanel" x1="0" y1="0" x2="1" y2="1">
          <stop offset="0" stop-color="var(--brown-mid)"/>
          <stop offset="1" stop-color="var(--brown-dark)"/>
        </linearGradient>
      </defs>
      <polygon points="332,570 1000,8 1000,570" fill="url(#brownPanel)"/>
      <line x1="318" y1="570" x2="992" y2="4" stroke="var(--accent-orange)" stroke-width="6"/>
    </svg>

    <div class="brand-name">Meadowlark Property Review</div>

    <div class="person">
      <div class="person-name">Daniel Reyes</div>
      <div class="person-title">CEO/Founder</div>
    </div>

    <div class="contact-block">
      <div class="address">4120 Birchwood Court<br>Springfield, Missouri 65804</div>
      <div class="contact-line">
        <span>417 555 0192</span>
        <svg class="contact-icon" viewBox="0 0 24 24" aria-hidden="true"><path d="M6.6 10.8c1.4 2.8 3.8 5.1 6.6 6.6l2.2-2.2c.3-.3.7-.4 1-.2 1.1.4 2.3.6 3.6.6.6 0 1 .4 1 1V20c0 .6-.4 1-1 1C10.6 21 3 13.4 3 4c0-.6.4-1 1-1h3.5c.6 0 1 .4 1 1 0 1.3.2 2.5.6 3.6.1.3 0 .7-.2 1z"/></svg>
      </div>
      <div class="contact-line">
        <span>417 555 0147</span>
        <svg class="contact-icon" viewBox="0 0 24 24" aria-hidden="true"><path d="M7 3h10v5H7z M4 9h16c1.1 0 2 .9 2 2v6h-4v4H6v-4H2v-6c0-1.1.9-2 2-2z M8 15v4h8v-4z"/></svg>
      </div>
      <div class="contact-line">
        <span>info@meadowlark.com</span>
        <svg class="contact-icon" viewBox="0 0 24 24" aria-hidden="true"><path d="M2 5h20v14H2z M4 7v.5l8 5.5 8-5.5V7z" fill-rule="evenodd"/></svg>
      </div>
      <div class="contact-line">
        <span>www.meadowlark.com</span>
        <svg class="contact-icon" viewBox="0 0 24 24" aria-hidden="true"><path d="M12 2a10 10 0 1 0 0 20 10 10 0 0 0 0-20zm-1 17.9A8 8 0 0 1 4.2 10L9 14.8V16c0 1.1.9 2 2 2zm6.9-2.5c-.3-.8-1-1.4-1.9-1.4h-1v-3c0-.6-.4-1-1-1H8v-2h2c.6 0 1-.4 1-1V7h2c1.1 0 2-.9 2-2v-.4a8 8 0 0 1 2.9 12.8z"/></svg>
      </div>
    </div>

    <div class="services">
      Residential appraisals | Home inspection<br>
      Pest inspection and radon gas measurement.
    </div>
  </section>
</main>
</body>
</html>
```